Millcrest PTA Website Design

We are working with Millcrest Elementary School PTA. They are a Parent Teacher Association that needs a new website design.

A Parent Teacher Association (PTA) is a volunteer organization that brings parents, teachers, and school staff together to support students and enhance their educational experience. PTAs organize fundraisers, sponsor school events, advocate for education policies, and foster stronger connections between families and schools.

Some sites to use for inspiration:

https://parentboardhub.com/demo/
https://nonprofits.kindlyfundr.com/blogs/more-great-pta-websites-you-should-copy
https://www.rvmxpta.com

Thank you for taking the time to consider designing a website for us. We are web developers based in Stockton and Los Angeles, CA, USA. Most of our projects go through the same process. Understanding this process may help you win a project with us. We custom-code all of our websites in-house. We don’t have any requirements as to what tools you use for your design, but we prefer Figma files. For any design that we label as four-stars, we send it to the client for review. The client picks the final design they want us to use. Once we complete this process, we will continue to show additional clients all the four-star sites and purchase them later. Your designs will have multiple chances to sell. For better chances of success, we ask that you follow these guidelines.

IMAGES:
If you use any images or icons in the design, we ask that you have a link to the asset so we can purchase the image/icon. Most of the designs we submit do not have the customer’s images on them unless they have some great images. Be creative; show us the feeling you are trying to portray with your image choices. Use any royalty-free site you choose. We subscribe to Adobe and mainly use their images, but we can purchase images outside of Adobe.

PLEASE NOTE: we will not submit designs to clients with watermarks on the images.

FONTS:
We ask that you identify the fonts used in the design. This can be done in a message if you want. We typically use Google Fonts and Adobe Fonts.

CONTENT:
We're always open to different content and ideas. We often submit designs with stock images so the client can see our vision. We typically take pictures after the website launch to use their images with our vision. Lorem Ipsum is fine for paragraphs, but we ask that you write the headers in correct English. We want to be able to show the vision and identify the sections of the website.

INSPIRATION:
We typically add a couple of links in the brief of websites we like to help you get started in your design.

REVISIONS:
We do not often ask for revisions of the designs unless we see something in the design that may not appeal to the client. If there are slight changes that we want to make, we do that in the development process.

FEEDBACK:
We rarely give feedback on designs during the design process. We are working on many website projects and do not have the time to provide feedback. We usually respond if your request is well thought out and asks specific questions, but a note asking “feedback, please” usually goes unanswered.

```html
<!DOCTYPE html>
<html lang="en">
<head>
<meta charset="utf-8">
<title>Millcrest PTA</title>
<link href="https://fonts.googleapis.com/css2?family=Montserrat:wght@600;700&family=Lato:ital,wght@0,400;0,700;1,400&display=swap" rel="stylesheet">
<style>
:root{
  --navy:#24418f;
  --navy-dark:#1d3577;
  --gold:#f8c22c;
  --ink:#1e1e1e;
  --muted:#4a4a4a;
  --light:#f4f6fb;
  --white:#ffffff;
  --line:#dde2ec;
}
*{box-sizing:border-box;margin:0;padding:0}
html,body{width:1200px;height:3931px;overflow:hidden}
body{position:relative;font-family:'Lato',sans-serif;color:var(--ink);background:var(--white)}
h1,h2{font-family:'Montserrat',sans-serif}
.section-title{position:absolute;left:0;width:1200px;text-align:center;font-size:40px;font-weight:600;color:var(--navy)}
.section-title::after{content:"";display:block;width:90px;height:4px;background:var(--navy);margin:14px auto 0}
.btn{position:absolute;display:flex;align-items:center;justify-content:center;font-family:'Lato',sans-serif;font-weight:700;font-size:17px;border-radius:3px;text-decoration:none}
.btn-gold{background:var(--gold);color:var(--ink)}

/* Header */
.site-header{position:absolute;left:0;top:0;width:1200px;height:714px;background:var(--navy)}
.brand{position:absolute;left:112px;top:48px;display:flex;align-items:center;gap:10px;color:var(--white);font-weight:700;font-size:24px}
.brand-mark{width:16px;height:16px;background:var(--white)}
.search{position:absolute;left:766px;top:20px;width:324px;height:36px;border:1px solid #c8d0e6;border-radius:3px;color:#e8ecf6;font-size:15px;padding:9px 14px}
.search svg{position:absolute;right:12px;top:8px}
.main-nav{position:absolute;right:110px;top:86px;display:flex;gap:36px;font-size:15px;color:var(--white)}
.hero{position:absolute;left:27px;top:136px;width:1146px;height:504px;border-radius:12px;overflow:hidden;
  background:
    radial-gradient(ellipse 260px 300px at 78% 38%, #f0c9a8 0%, rgba(240,201,168,0) 70%),
    radial-gradient(ellipse 420px 260px at 70% 85%, #f2b321 0%, rgba(242,179,33,0) 75%),
    radial-gradient(ellipse 200px 500px at 96% 50%, #f5c12a 0%, rgba(245,193,42,0) 80%),
    radial-gradient(ellipse 380px 200px at 20% 88%, #9b4d3a 0%, rgba(155,77,58,0) 80%),
    radial-gradient(ellipse 500px 260px at 25% 15%, #6f9a7c 0%, rgba(111,154,124,0) 80%),
    linear-gradient(120deg,#44739a 0%,#7a9a84 40%,#d7ae52 70%,#e6b93a 100%)}
.hero-photo{position:absolute;inset:0;background:linear-gradient(90deg,rgba(20,30,60,.45) 0%,rgba(20,30,60,.12) 50%,rgba(0,0,0,0) 100%)}
.hero h1{position:absolute;left:68px;top:100px;font-size:55px;line-height:64px;font-weight:700;color:var(--white);text-shadow:0 2px 6px rgba(0,0,0,.35)}
.hero p{position:absolute;left:68px;top:250px;font-size:17px;color:var(--white);text-shadow:0 1px 4px rgba(0,0,0,.4)}
.hero .btn{left:69px;top:297px;width:140px;height:47px;background:var(--navy);color:var(--white);font-weight:400}

/* Cards */
.card{position:absolute;width:309px;height:353px;background:var(--white);border-radius:4px;box-shadow:0 1px 6px rgba(0,0,0,.15);overflow:hidden;text-align:center}
.card-media{height:222px}
.card h3{font-weight:700;font-size:21px;margin-top:10px;color:var(--ink)}
.card p{font-size:14.5px;line-height:26px;color:var(--muted);height:52px;overflow:hidden;padding:0 16px;margin-top:4px}
.card a{display:inline-block;margin-top:2px;font-size:14px;font-style:italic;color:var(--ink);text-decoration:underline}
.arrow{position:absolute;width:28px;height:28px;border:1.5px solid var(--navy);border-radius:50%;display:flex;align-items:center;justify-content:center}

/* Store */
.store{position:absolute;left:0;top:1327px;width:1200px;height:474px;background:var(--navy);color:var(--white)}
.store h2{position:absolute;left:0;width:1200px;top:72px;text-align:center;font-size:40px;font-weight:600}
.store-art{position:absolute;left:978px;top:8px;width:214px;height:150px;border-radius:18px;
  background:
    radial-gradient(ellipse 70px 60px at 28% 40%, #f2d3a0 0%, rgba(242,211,160,0) 80%),
    radial-gradient(ellipse 70px 60px at 75% 45%, #f4b9a0 0%, rgba(244,185,160,0) 80%),
    linear-gradient(160deg,#3b5aa8 0%,#e7c067 45%,#d8453c 75%,#f3eeea 100%)}
.store-text{position:absolute;left:150px;top:165px;width:900px;text-align:center;font-size:15px;line-height:29px}
.store .btn{left:531px;top:341px;width:140px;height:47px}

/* Contact */
.contact{position:absolute;left:0;top:2886px;width:1200px;height:664px;background:var(--light)}
.contact-lead{position:absolute;left:0;width:1200px;top:172px;text-align:center;font-size:14.5px}
.map{position:absolute;left:111px;top:217px;width:445px;height:287px;border-radius:8px;border:1px solid var(--line);
  background:
    radial-gradient(ellipse 160px 90px at 55% 70%, #cfe7c9 0%, rgba(207,231,201,0) 80%),
    radial-gradient(ellipse 120px 80px at 25% 45%, #d6ead0 0%, rgba(214,234,208,0) 80%),
    radial-gradient(ellipse 180px 120px at 70% 25%, #e6e9f2 0%, rgba(230,233,242,0) 80%),
    linear-gradient(135deg,#f1f2f4,#e3e8e4 50%,#eceef2)}
.info{position:absolute;display:flex;align-items:center;gap:10px;font-size:15px}
.form-card{position:absolute;left:644px;top:217px;width:446px;height:356px;background:var(--white);border-radius:14px;box-shadow:0 1px 6px rgba(0,0,0,.06)}
.field{position:absolute;left:29px;width:388px;height:48px;border:1px solid var(--line);border-radius:6px;display:flex;align-items:center;gap:10px;padding-left:22px;font-size:14.5px;color:#555}
.field .chev{position:absolute;right:20px;top:17px}
.form-card .btn{left:37px;top:285px;width:136px;height:46px;color:var(--white);font-weight:400}

/* Footer */
.site-footer{position:absolute;left:0;top:3550px;width:1200px;height:381px;background:var(--navy);color:var(--white)}
.footer-brand{position:absolute;left:112px;top:135px;display:flex;align-items:center;gap:10px;font-weight:700;font-size:26px}
.footer-col{position:absolute;top:100px;font-size:14.5px}
.footer-col h4{font-weight:700;font-size:19px;text-decoration:underline;margin-bottom:14px}
.footer-col ul{list-style:none}
.footer-col li{line-height:34px;position:relative;padding-left:24px}
.footer-col li::before{content:"";position:absolute;left:2px;top:14px;width:8px;height:8px;border-radius:50%;background:var(--white)}
.news-input{width:220px;height:40px;background:var(--white);border-radius:3px;color:#333;padding:11px 22px;margin-top:14px}
.news-btn{width:118px;height:40px;background:var(--gold);border-radius:3px;display:flex;align-items:center;justify-content:center;margin-top:10px;font-size:17px}
.c-line{display:flex;gap:10px;line-height:22px;margin-bottom:16px}
.c-line svg{flex:none;margin-top:2px}
.footer-rule{position:absolute;left:112px;top:330px;width:978px;height:1px;background:rgba(255,255,255,.35)}
.socials{position:absolute;left:108px;top:354px;display:flex;gap:16px}
.socials span{width:20px;height:20px;border-radius:50%;border:2px solid var(--white)}
.copyright{position:absolute;right:110px;top:356px;font-size:14.5px}

/* Photo tones */
.m-give{background:radial-gradient(ellipse 90px 110px at 40% 55%,#3f74c4 0%,rgba(63,116,196,0) 80%),radial-gradient(ellipse 120px 90px at 80% 80%,#3a3f4a 0%,rgba(58,63,74,0) 80%),radial-gradient(ellipse 90px 90px at 12% 60%,#b6413a 0%,rgba(182,65,58,0) 80%),linear-gradient(135deg,#ecebe7,#d9d2c6 50%,#c9b6a2)}
.m-carnival{background:radial-gradient(ellipse 120px 40px at 50% 35%,#2a8a8a 0%,rgba(42,138,138,0) 85%),radial-gradient(ellipse 150px 50px at 50% 12%,#d8332b 0%,rgba(216,51,43,0) 85%),linear-gradient(180deg,#e8443a 0%,#f5d98d 40%,#f7e4b2 70%,#ecc27a 100%)}
.m-volunteer{background:radial-gradient(ellipse 110px 70px at 50% 35%,#cfd8c7 0%,rgba(207,216,199,0) 80%),radial-gradient(ellipse 160px 70px at 50% 90%,#4e3b28 0%,rgba(78,59,40,0) 85%),linear-gradient(180deg,#7da35a 0%,#a7b88d 35%,#6c8a3e 70%,#5a4a30 100%)}
.m-art{background:radial-gradient(ellipse 90px 110px at 30% 45%,#f0e6da 0%,rgba(240,230,218,0) 80%),radial-gradient(ellipse 100px 90px at 80% 60%,#e4e6ea 0%,rgba(228,230,234,0) 80%),linear-gradient(135deg,#b99d7c,#8c7560 50%,#6f6a68)}
.m-supplies{background:radial-gradient(ellipse 80px 60px at 25% 30%,#d83a3a 0%,rgba(216,58,58,0) 80%),radial-gradient(ellipse 80px 60px at 75% 25%,#2f9a55 0%,rgba(47,154,85,0) 80%),radial-gradient(ellipse 90px 60px at 60% 75%,#2f7fc0 0%,rgba(47,127,192,0) 80%),linear-gradient(135deg,#d3a35c,#e3b46b 50%,#c8904a)}
.m-trips{background:radial-gradient(ellipse 90px 80px at 70% 35%,#fff1b8 0%,rgba(255,241,184,0) 80%),radial-gradient(ellipse 60px 50px at 45% 50%,#e7a21d 0%,rgba(231,162,29,0) 85%),radial-gradient(ellipse 160px 60px at 50% 92%,#a58a6a 0%,rgba(165,138,106,0) 85%),linear-gradient(180deg,#7b9a56 0%,#3f5a2a 50%,#8a7255 100%)}
.m-assembly{background:radial-gradient(ellipse 80px 110px at 62% 55%,#6d4a37 0%,rgba(109,74,55,0) 80%),radial-gradient(ellipse 90px 70px at 62% 90%,#e9b94a 0%,rgba(233,185,74,0) 85%),linear-gradient(135deg,#6c6a7a,#9c7a62 50%,#c4a888)}
.m-music{background:radial-gradient(ellipse 70px 60px at 25% 70%,#f2eee6 0%,rgba(242,238,230,0) 80%),radial-gradient(ellipse 90px 60px at 55% 40%,#c9a34a 0%,rgba(201,163,74,0) 80%),linear-gradient(135deg,#8d93a6,#c3b4a6 50%,#6f7f95)}
.m-library{background:radial-gradient(ellipse 70px 70px at 50% 50%,#c7b392 0%,rgba(199,179,146,0) 85%),radial-gradient(ellipse 140px 120px at 50% 50%,#3c4654 0%,rgba(60,70,84,0) 90%),linear-gradient(135deg,#6b3d2a,#a0744f 50%,#4a2f25)}
</style>
</head>
<body>

<header class="site-header">
  <div class="brand"><span class="brand-mark"></span>Millcrest PTA</div>
  <div class="search">Search
    <svg width="18" height="18" viewBox="0 0 24 24" fill="none" stroke="#fff" stroke-width="2.2"><circle cx="10" cy="10" r="7"/><path d="M15 15l6 6"/></svg>
  </div>
  <nav class="main-nav">
    <span>Home</span><span>PTA and YOU!</span><span>Millcrest PTA Store</span><span>PTA-Funded Progams</span><span>Blue and White</span><span>Contact Us</span>
  </nav>
  <section class="hero" role="img" aria-label="Smiling young student playing on a bright yellow playground slide">
    <div class="hero-photo"></div>
    <h1>Together, We<br>Make Magic Happen</h1>
    <p>Join our team of amazing volunteers and bring smiles to our Millcrest Lions!</p>
    <a class="btn" href="#">Join the PTA</a>
  </section>
</header>

<h2 class="section-title" style="top:788px">PTA and You!</h2>
<div class="arrow" style="left:41px;top:1051px"><svg width="10" height="12" viewBox="0 0 10 12"><path d="M7 1L2 6l5 5" fill="none" stroke="#24418f" stroke-width="1.6"/></svg></div>
<div class="arrow" style="left:1131px;top:1051px"><svg width="10" height="12" viewBox="0 0 10 12"><path d="M3 1l5 5-5 5" fill="none" stroke="#24418f" stroke-width="1.6"/></svg></div>
<article class="card" style="left:111px;top:888px"><div class="card-media m-give" role="img" aria-label="Students giving high fives in a classroom"></div><h3>Give Back!</h3><p>PTA works hard to provide an incredible array of programs and experiences for all</p><a href="#">Read More</a></article>
<article class="card" style="left:445px;top:888px"><div class="card-media m-carnival" role="img" aria-label="Fall costume carnival event poster"></div><h3>2024 Fall Carnival</h3><p>Join the fun and support the Millcrest 6th Graders! Carnival games, tasty food,</p><a href="#">Read More</a></article>
<article class="card" style="left:779px;top:888px"><div class="card-media m-volunteer" role="img" aria-label="Volunteers planting trees in a park"></div><h3>Volunteer with PTA!</h3><p>Become a PTA volunteer today! Join the Board... Plan an activity or event...</p><a href="#">Read More</a></article>

<section class="store">
  <div class="store-art" role="img" aria-label="Illustration of two children having a picnic on a checkered blanket"></div>
  <h2>Millcrest PTA Store</h2>
  <p class="store-text">Don't be caught unprepared! Join PTA and make a difference.<br>Yearbooks are where it's at!&nbsp; Snap those photos of school events and fun days at Millcrest then send them over to<br>millcrestyearbook@example.com!<br>Also, you can't leave home without your Millcrest Spirit Wear! Choose your style and size below then check out using your<br>credit/debit card or PayWallet. We can't wait to see you show off your Lion Pride...even if it's only virtually right now!</p>
  <a class="btn btn-gold" href="#">View Cart</a>
</section>

<h2 class="section-title" style="top:1876px">PTA-Funded Programs</h2>
<article class="card" style="left:111px;top:1978px"><div class="card-media m-art" role="img" aria-label="Students working together at a desk"></div><h3>Art Program</h3><p>Through fundraising and generous donations, our PTA fully funds our entire</p><a href="#">Read More</a></article>
<article class="card" style="left:445px;top:1978px"><div class="card-media m-supplies" role="img" aria-label="Colorful school supplies on a desk"></div><h3>Teacher Supplies</h3><p>With education budgets being tightened, we like to support our teachers in the big</p><a href="#">Read More</a></article>
<article class="card" style="left:779px;top:1978px"><div class="card-media m-trips" role="img" aria-label="Yellow school bus on a wooden bridge at sunset"></div><h3>Field Trips</h3><p>Out-of-class experiences are often the ones that really drive home the lessons</p><a href="#">Read More</a></article>
<article class="card" style="left:111px;top:2363px"><div class="card-media m-assembly" role="img" aria-label="Students sitting together at a school assembly"></div><h3>Assemblies</h3><p>Anti-bullying, Silver Acorn, The Kind Kid Show...all these assemblies and more</p><a href="#">Read More</a></article>
<article class="card" style="left:445px;top:2363px"><div class="card-media m-music" role="img" aria-label="Children playing instruments in a music class"></div><h3>Music</h3><p>From penny whistles and lessons to piano accompaniment for our chorus,</p><a href="#">Read More</a></article>
<article class="card" style="left:779px;top:2363px"><div class="card-media m-library" role="img" aria-label="Tunnel of library books"></div><h3>Library Books</h3><p>Out-of-class experiences are often the ones that really drive home the lessons</p><a href="#">Read More</a></article>
<a class="btn btn-gold" href="#" style="left:531px;top:2746px;width:140px;height:47px">View More</a>

<section class="contact">
  <h2 class="section-title" style="top:78px">Get in Touch</h2>
  <p class="contact-lead">Have a question, want to volunteer, or need event details? We'd love to hear from you — reach out anytime!</p>
  <div class="map" role="img" aria-label="Street map showing the PTA office location"></div>
  <div class="info" style="left:111px;top:522px"><svg width="20" height="20" viewBox="0 0 20 20"><circle cx="10" cy="10" r="10" fill="#24418f"/><path d="M6.5 5.5l2 0 1 2.5-1.2 1a6 6 0 003 3l1-1.2 2.5 1v2c-4.5.5-9-4-8.3-8.3z" fill="#fff"/></svg>(209) 555-0148</div>
  <div class="info" style="left:327px;top:522px"><svg width="20" height="20" viewBox="0 0 20 20"><circle cx="10" cy="10" r="10" fill="#24418f"/><rect x="5" y="6.5" width="10" height="7" fill="none" stroke="#fff" stroke-width="1.3"/><path d="M5 7l5 3.5L15 7" fill="none" stroke="#fff" stroke-width="1.3"/></svg>millcrestpta@example.com</div>
  <div class="info" style="left:111px;top:561px"><svg width="20" height="20" viewBox="0 0 20 20"><circle cx="10" cy="10" r="10" fill="#24418f"/><path d="M10 4a4 4 0 014 4c0 3-4 7-4 7s-4-4-4-7a4 4 0 014-4z" fill="#fff"/><circle cx="10" cy="8" r="1.5" fill="#24418f"/></svg>1480 Orchard Lane Rivermont, CA 95300</div>
  <form class="form-card">
    <div class="field" style="top:24px"><svg width="16" height="16" viewBox="0 0 16 16" fill="#777"><circle cx="8" cy="5" r="3.5"/><path d="M1 15c0-4 3-6 7-6s7 2 7 6z"/></svg>Name</div>
    <div class="field" style="top:88px"><svg width="18" height="14" viewBox="0 0 18 14"><rect x="1" y="1" width="16" height="12" fill="#777"/><path d="M1 1l8 6 8-6" fill="none" stroke="#fff" stroke-width="1.4"/></svg>Email</div>
    <div class="field" style="top:152px"><svg width="16" height="16" viewBox="0 0 16 16" fill="none" stroke="#777" stroke-width="1.5"><rect x="1" y="2" width="14" height="13"/><path d="M1 6h14M5 0v4M11 0v4"/></svg>What is thirteen minus 6?<svg class="chev" width="12" height="8" viewBox="0 0 12 8"><path d="M1 1l5 5 5-5" fill="none" stroke="#333" stroke-width="1.5"/></svg></div>
    <div class="field" style="top:216px"><svg width="16" height="16" viewBox="0 0 20 20"><path d="M3 2h4l2 5-2 1.5a10 10 0 004.5 4.5L13 11l5 2v4C9 18 2 11 3 2z" fill="#777"/></svg>Phone Number</div>
    <a class="btn btn-gold" href="#">Submit</a>
  </form>
</section>

<footer class="site-footer">
  <div class="footer-brand"><span class="brand-mark"></span>Millcrest PTA</div>
  <div class="footer-col" style="left:364px"><h4>Quick Links</h4><ul><li>Home</li><li>PTA and YOU!</li><li>Millcrest PTA Store</li><li>PTA-Funded Progams</li><li>Blue and White</li></ul></div>
  <div class="footer-col" style="left:592px;width:230px"><h4>Newsletter</h4><p style="line-height:22px;padding-left:4px">Subscribe to our latest newsletter to get news about special discounts.</p><div class="news-input">Email</div><div class="news-btn">Subscribe</div></div>
  <div class="footer-col" style="left:868px;width:232px"><h4>Contact Us</h4>
    <div class="c-line"><svg width="18" height="18" viewBox="0 0 20 20"><circle cx="10" cy="10" r="10" fill="#fff"/><path d="M10 4a4 4 0 014 4c0 3-4 7-4 7s-4-4-4-7a4 4 0 014-4z" fill="#24418f"/></svg><span>22 Linden Street, Brookfield,<br>NY 10020,</span></div>
    <div class="c-line"><svg width="18" height="18" viewBox="0 0 20 20"><circle cx="10" cy="10" r="10" fill="#fff"/><rect x="5" y="6.5" width="10" height="7" fill="#24418f"/></svg><span>hello@millcrestpta.org</span></div>
    <div class="c-line"><svg width="18" height="18" viewBox="0 0 20 20"><circle cx="10" cy="10" r="10" fill="#fff"/><path d="M6.5 5.5l2 0 1 2.5-1.2 1a6 6 0 003 3l1-1.2 2.5 1v2c-4.5.5-9-4-8.3-8.3z" fill="#24418f"/></svg><span>+1 (800) 555-0199</span></div>
  </div>
  <div class="footer-rule"></div>
  <div class="socials" aria-label="Social links"><span></span><span></span><span></span><span></span></div>
  <p class="copyright">© 2025 Millcrest PTA · All Rights Reserved</p>
</footer>

</body>
</html>
```